Redesign of business card for Cedar Ridge Mechanical

We are looking for a new design for our business cards for Cedar Ridge Mechanical. We are a plumbing & HVAC construction company, operating on the West Coast of Canada and USA. Logo attached.
Industry/Entity Type
Construction - Plumbing & HVAC
Contact Information for Business Card
Name, address, phone numbers, email, website address
Look and feel
Each slider illustrates characteristics of the customer's brand and the style your logo design should communicate.

```html
<!DOCTYPE html>
<html lang="en">
<head>
<meta charset="UTF-8">
<title>Cedar Ridge Mechanical – Business Card</title>
<link href="https://fonts.googleapis.com/css2?family=Montserrat:wght@300;700&family=Lato:wght@400&display=swap" rel="stylesheet">
<style>
  :root {
    --canvas: #2b2b2b;
    --card-dark: #161616;
    --card-light: #ffffff;
    --ink: #111111;
    --ink-soft: #333333;
    --mark-dark: #3a3a3a;
    --mark-light: #3c3c3c;
    --rule: #555555;
  }
  * { margin: 0; padding: 0; box-sizing: border-box; }
  html, body {
    width: 1200px; height: 895px; overflow: hidden;
    background: var(--canvas);
  }
  .canvas {
    width: 1200px; height: 895px;
    display: flex; flex-direction: column;
    align-items: center; justify-content: center; gap: 35px;
  }
  .card {
    width: 700px; height: 400px;
    position: relative;
    box-shadow: 0 10px 30px rgba(0,0,0,.45);
  }
  .card--front { background: var(--card-dark); display: flex; align-items: center; justify-content: center; }
  .card--back { background: var(--card-light); }

  .brand {
    display: flex; align-items: center; gap: 14px;
    font-family: 'Lato', sans-serif; font-weight: 400;
    text-transform: uppercase; letter-spacing: 2px;
  }
  .brand__square { width: 22px; height: 22px; flex: none; }
  .card--front .brand { color: var(--mark-dark); font-size: 26px; }
  .card--front .brand__square { background: var(--mark-dark); }

  .card--back .brand {
    position: absolute; left: 0; top: 0; bottom: 0; width: 368px;
    justify-content: center;
    color: var(--mark-light); font-size: 24px; line-height: 30px;
  }
  .card--back .brand__square { background: var(--mark-light); width: 20px; height: 20px; }
  .brand__line { display: block; }

  .divider {
    position: absolute; left: 368px; top: 95px;
    width: 1.5px; height: 210px; background: var(--rule);
  }

  .contact {
    position: absolute; left: 398px; top: 92px;
    color: var(--ink);
  }
  .contact__name {
    font-family: 'Montserrat', sans-serif; font-weight: 700;
    font-size: 25px; letter-spacing: 1px; text-transform: uppercase;
  }
  .contact__title {
    font-family: 'Montserrat', sans-serif; font-weight: 300;
    font-size: 17px; letter-spacing: 1px; text-transform: uppercase;
    color: var(--ink-soft); margin-top: 2px;
  }
  .contact__list {
    list-style: none; margin-top: 20px;
    font-family: 'Lato', sans-serif; font-size: 16px; line-height: 24px;
  }
  .contact__list li { display: flex; align-items: center; gap: 10px; }
  .contact__list svg { width: 15px; height: 15px; flex: none; fill: var(--ink); }
  .contact__address {
    font-family: 'Lato', sans-serif; font-size: 16px; line-height: 22px;
    margin-top: 14px;
  }
</style>
</head>
<body>
<main class="canvas">
  <section class="card card--front" aria-label="Card front">
    <div class="brand"><span class="brand__square"></span><span>Cedar Ridge Mechanical</span></div>
  </section>

  <section class="card card--back" aria-label="Card back">
    <div class="brand"><span class="brand__square"></span><span><span class="brand__line">Cedar Ridge</span><span class="brand__line">Mechanical</span></span></div>
    <div class="divider"></div>
    <div class="contact">
      <h1 class="contact__name">Daniel Hayes</h1>
      <p class="contact__title">Managing Director</p>
      <ul class="contact__list">
        <li>
          <svg viewBox="0 0 16 16" aria-hidden="true"><path d="M3.6 1.2l2.3 2.6-1.3 1.9c.9 2 2.5 3.6 4.6 4.6l1.9-1.3 2.6 2.3-1.4 2.2C6.9 13.3 2.7 9.1 1.4 3z"/></svg>
          <span>044-555 019 246</span>
        </li>
        <li>
          <svg viewBox="0 0 16 16" aria-hidden="true"><path d="M1 3h14v10H1z M2 4.2v.5l6 4 6-4v-.5z" fill-rule="evenodd"/></svg>
          <span>info@cedarridgemech.com</span>
        </li>
        <li>
          <svg viewBox="0 0 16 16" aria-hidden="true"><circle cx="8" cy="8" r="7"/><path d="M4 5c1 0 2 1 1.5 2S6 9 7 9.5 6 13 5 12 3 7 4 5zM10 3c1 1 3 2 2.5 4S10 8 10 6.5 9 4 10 3z" fill="#fff"/></svg>
          <span>www.cedarridgemech.com</span>
        </li>
      </ul>
      <p class="contact__address">421, Address line goes here<br>45452, Country name</p>
    </div>
  </section>
</main>
</body>
</html>
```